Veldmark Supplies Business Card

Professional business card that stand out to our potential customers. Front and back with clean modern design

Industry/Entity Type

Oil and gas

Contact Information for Business Card

Name, address, website , office phone and cell number

Requirements
Must have
• Editable files for each employee

```html
<!DOCTYPE html>
<html lang="en">
<head>
<meta charset="utf-8">
<title>Veldmark Supplies Business Card</title>
<link href="https://fonts.googleapis.com/css2?family=Arimo:wght@400;700&display=swap" rel="stylesheet">
<style>
  :root {
    --backdrop: #3c3c3c;
    --card-dark: #262626;
    --card-dark-edge: #1b1b1b;
    --cyan: #02afd1;
    --white: #ffffff;
    --accent-red: #e5161d;
    --steel: #8c8c8c;
    --steel-dim: #4a4a4a;
  }
  * { box-sizing: border-box; margin: 0; padding: 0; }
  html, body { width: 1200px; height: 803px; overflow: hidden; }
  body {
    background: var(--backdrop);
    font-family: "Arimo", Arial, sans-serif;
    display: flex;
    align-items: center;
    justify-content: center;
    gap: 48px;
  }
  .card {
    position: relative;
    width: 525px;
    height: 300px;
    border-radius: 18px;
    overflow: hidden;
  }
  /* Front */
  .card-front { background: var(--cyan); }
  .front-dark-field { position: absolute; inset: 0; width: 100%; height: 100%; }
  .front-brand {
    position: absolute;
    top: 30px;
    right: 34px;
    display: flex;
    align-items: center;
    gap: 8px;
  }
  .brand-square {
    width: 14px; height: 14px;
    background: var(--accent-red);
  }
  .brand-name {
    font-weight: 700;
    font-size: 17px;
    letter-spacing: 2px;
    text-transform: uppercase;
    color: var(--white);
  }
  .contact-block {
    position: absolute;
    top: 78px;
    left: 250px;
    color: var(--white);
  }
  .person-name {
    font-weight: 700;
    font-size: 24px;
    letter-spacing: 0.5px;
    text-transform: uppercase;
  }
  .person-title { font-size: 12px; margin-top: 2px; }
  .address { font-size: 12.5px; line-height: 1.35; margin-top: 16px; }
  .contact-list { list-style: none; margin-top: 12px; font-size: 12.5px; line-height: 1.5; }
  .contact-list li { display: flex; align-items: center; gap: 7px; }
  .contact-list svg { width: 11px; height: 11px; flex: none; }
  /* Back */
  .card-back {
    background: var(--card-dark);
    display: flex;
    flex-direction: column;
    align-items: center;
    justify-content: center;
    gap: 26px;
  }
  .back-square {
    width: 86px; height: 86px;
    border: 2px solid var(--steel-dim);
    background: var(--card-dark-edge);
  }
  .back-brand {
    font-weight: 700;
    font-size: 28px;
    letter-spacing: 3px;
    text-transform: uppercase;
    color: var(--steel);
  }
</style>
</head>
<body>
  <section class="card card-front" aria-label="Business card front">
    <svg class="front-dark-field" viewBox="0 0 525 300" preserveAspectRatio="none" aria-hidden="true">
      <polygon points="0,118 200,118 250,300 0,300" fill="var(--card-dark)"/>
    </svg>
    <div class="front-brand">
      <span class="brand-square"></span>
      <span class="brand-name">Veldmark Supplies</span>
    </div>
    <div class="contact-block">
      <h1 class="person-name">Daniel Harker</h1>
      <p class="person-title">President</p>
      <p class="address">4412 Birchwood Road<br>Calgary, Canada 56120</p>
      <ul class="contact-list">
        <li>
          <svg viewBox="0 0 12 12"><path d="M2 1h3l1 3-2 1a7 7 0 0 0 3 3l1-2 3 1v3c-6 0-10-4-10-10z" fill="var(--accent-red)"/></svg>
          555-214-3087
        </li>
        <li>
          <svg viewBox="0 0 12 12"><rect x="3" y="0.5" width="6" height="11" rx="1" fill="none" stroke="var(--accent-red)" stroke-width="1.4"/></svg>
          555-862-4190
        </li>
        <li>
          <svg viewBox="0 0 12 12"><rect x="0.5" y="2" width="11" height="8" fill="var(--accent-red)"/><path d="M1 2.5 6 6.5 11 2.5" fill="none" stroke="var(--white)" stroke-width="1"/></svg>
          info@veldmarksupplies.com
        </li>
        <li>
          <svg viewBox="0 0 12 12"><circle cx="6" cy="6" r="5.5" fill="var(--accent-red)"/><path d="M0.5 6h11M6 0.5c-3 3-3 8 0 11M6 0.5c3 3 3 8 0 11" fill="none" stroke="var(--white)" stroke-width="0.8"/></svg>
          www.veldmarksupplies.com
        </li>
      </ul>
    </div>
  </section>

  <section class="card card-back" aria-label="Business card back">
    <span class="back-square"></span>
    <p class="back-brand">Veldmark Supplies</p>
  </section>
</body>
</html>
```